Flyer Design for Private Car Service

Flyer should cater to Business Travelers and Executives who travel Business Class or First Class.
Flyer should include images attached.
Flyer should include the below text
Dallas to Austin
Quorvan Ride
• Travel Dallas to Austin in a new 2025 Norvak Tressel for $499 one-way
• Trip includes a Uniformed Chauffeur who has a Commercial Drivers License (CDL)
• You can Schedule Chauffeur Pickup at Your Home in Dallas
• Our Chauffeur will Drop You Off at Your Final Destination in Austin
• You can Schedule Chauffeur Return Pickup in Austin and Return Back to Dallas.
• We offer Faster Times on Door-to-Door Travel than Bluequill Airways
• We offer Comparable Prices on Door-to-Door Travel Times than Bluequill Airways
• All of our trips are insured with $500k of commercial auto insurance
• Our Passengers can Talk on Cell Phone & Conduct Kavlo calls Throughout Travel
• Our Passengers have Maximum Privacy, Comfort and First-Class Amenities.
• Our Passengers Avoid Marrow Pike Airfield and QHN Airport hassles & delays
• Member Tellbrook Chamber of Commerce, Pindle Chamber of Commerce.
• Book your trip today at www.quorvanride.example
Target Market(s)
Business Travelers
Look and feel

```html
<!DOCTYPE html>
<html lang="en">
<head>
<meta charset="utf-8">
<title>Quorvan Ride – Dallas to Austin</title>
<link href="https://fonts.googleapis.com/css2?family=Open+Sans:wght@400;800&display=swap" rel="stylesheet">
<style>
  :root {
    --ink: #0b0b0b;
    --white: #ffffff;
    --red: #e8232e;
    --red-soft: #ee3650;
    --brand-ink: #1c1c1c;
  }
  html, body { margin: 0; padding: 0; overflow: hidden; background: var(--white); }
  .flyer {
    position: relative;
    width: 927px; height: 1200px;
    overflow: hidden;
    background: var(--ink);
    font-family: "Open Sans", sans-serif;
  }
  .hero-photo {
    position: absolute; left: 0; top: 0;
    width: 927px; height: 530px;
    background: linear-gradient(180deg,
      #b5afab 0%, #ccc6c2 10%, #c9c3bf 22%,
      #6d6a69 26%, #4a4848 34%, #5c5a5a 42%,
      #2a2626 52%, #7a3a3a 60%, #3b3838 66%,
      #b3aca7 72%, #aaa39e 85%, #9c9590 100%);
  }
  .shapes { position: absolute; left: 0; top: 0; }
  .brand {
    position: absolute; left: 40px; top: 58px; width: 215px;
    display: flex; align-items: center; justify-content: center; gap: 10px;
    font-size: 30px; font-weight: 400; color: var(--brand-ink);
    letter-spacing: 0.5px; line-height: 1.2;
  }
  .brand-dot { width: 14px; height: 14px; border-radius: 50%; background: var(--red); flex: none; }
  .features {
    position: absolute; left: 0; top: 571px; width: 927px;
    margin: 0; padding: 0; list-style: none;
    text-align: center; color: var(--white);
    font-size: 18.6px; line-height: 44px;
  }
  .cta {
    position: absolute; left: 0; top: 1160px; width: 927px; margin: 0;
    text-align: center; color: var(--white);
    font-size: 22px; font-weight: 800; line-height: 32px;
  }
  .cta a { color: var(--white); text-decoration: underline; text-underline-offset: 3px; }
  .code {
    position: absolute; right: 16px; top: 1169px;
    color: var(--white); font-size: 11px;
  }
</style>
</head>
<body>
<div class="flyer">
  <div class="hero-photo" role="img" aria-label="Photo of a black, a white and a red SUV parked in front of a light office building with large windows, with four uniformed chauffeurs standing between them on the pavement"></div>

  <svg class="shapes" width="927" height="1200" viewBox="0 0 927 1200" aria-hidden="true">
    <path d="M0,518 Q463,462 927,518 L927,1200 L0,1200 Z" fill="var(--ink)"/>
    <path d="M0,515 Q463,458 927,515" fill="none" stroke="var(--red)" stroke-width="3"/>
    <path d="M0,519 Q463,463 927,519" fill="none" stroke="var(--white)" stroke-width="2.5"/>

    <path d="M0,1065 Q463,1230 927,1065 L927,1200 L0,1200 Z" fill="var(--red)"/>
    <path d="M0,1065 Q463,1230 927,1065" fill="none" stroke="var(--white)" stroke-width="3"/>
    <path d="M0,1098 Q463,1198 927,1098 L927,1200 L0,1200 Z" fill="var(--red-soft)"/>
    <path d="M0,1098 Q463,1198 927,1098" fill="none" stroke="var(--white)" stroke-width="2.5"/>
  </svg>

  <div class="brand"><span class="brand-dot"></span>Quorvan Ride</div>

  <ul class="features">
    <li>• Travel Dallas to Austin in a new 2025 Norvak Tressel for $499 one-way</li>
    <li>• Trip includes a Uniformed Chauffeur who has a Commercial Drivers License (CDL)</li>
    <li>• You can Schedule Chauffeur Pickup at Your Home in Dallas</li>
    <li>• Our Chauffeur will Drop You Off at Your Final Destination in Austin</li>
    <li>• You can Schedule Chauffeur Return Pickup in Austin and Return Back to Dallas.</li>
    <li>• We offer Faster Times on Door-to-Door Travel than Bluequill Airways</li>
    <li>• We offer Comparable Prices on Door-to-Door Travel Times than Bluequill Airways</li>
    <li>• All of our trips are insured with $500k of commercial auto insurance</li>
    <li>• Our Passengers can Talk on Cell Phone &amp; Conduct Kavlo calls Throughout Travel</li>
    <li>• Our Passengers have Maximum Privacy, Comfort and First-Class Amenities.</li>
    <li>• Our Passengers Avoid Marrow Pike Airfield and QHN Airport hassles &amp; delays</li>
    <li>• Member Tellbrook Chamber of Commerce, Pindle Chamber of Commerce.</li>
  </ul>

  <p class="cta">Book your trip today at <a href="#">www.quorvanride.example</a></p>
  <span class="code">C58</span>
</div>
</body>
</html>
```